Veldmark Supplies Business Card

Professional business card that stand out to our potential customers. Front and back with clean modern design

Industry/Entity Type

Oil and gas

Contact Information for Business Card

Name, address, website , office phone and cell number

Requirements
Must have
• Editable files for each employee

```html
<!DOCTYPE html>
<html lang="en">
<head>
<meta charset="utf-8">
<title>Veldmark Supplies Business Card</title>
<link rel="stylesheet" href="https://fonts.googleapis.com/css2?family=Roboto:wght@400;500;700;900&display=swap">
<style>
  :root {
    --stage: #2a2a2a;
    --paper: #f7f7f5;
    --brand-red: #e0232b;
    --brand-blue: #1fa9d3;
    --ink: #2b2b2b;
    --white: #ffffff;
  }
  * { margin: 0; padding: 0; box-sizing: border-box; }
  html, body {
    width: 1200px; height: 852px; overflow: hidden;
    background: var(--stage);
    font-family: "Roboto", Arial, sans-serif;
  }
  .stage {
    position: relative; width: 1200px; height: 852px;
    display: flex; align-items: center; justify-content: center; gap: 40px;
  }
  .card {
    position: relative; width: 520px; height: 297px;
    background: var(--paper); border-radius: 18px; overflow: hidden;
  }
  .card-art { position: absolute; inset: 0; width: 100%; height: 100%; }

  /* brand name block (stands where the mark sits) */
  .brand {
    position: absolute; display: flex; align-items: center; gap: 10px;
  }
  .brand-square { background: var(--brand-blue); }
  .brand-name {
    font-weight: 900; color: var(--brand-red);
    text-transform: uppercase; letter-spacing: 0.04em; line-height: 1;
  }
  .card-front .brand { left: 50%; top: 50%; transform: translate(-50%, -50%); }
  .card-front .brand-square { width: 26px; height: 26px; }
  .card-front .brand-name { font-size: 30px; }

  .card-front .edge-stripe {
    position: absolute; left: 0; right: 0; bottom: 0; height: 6px;
    background: linear-gradient(90deg, var(--brand-red) 0 55%, var(--brand-blue) 55% 100%);
  }

  .card-back .brand { left: 26px; bottom: 34px; }
  .card-back .brand-square { width: 20px; height: 20px; }
  .card-back .brand-name { font-size: 23px; }

  .holder {
    position: absolute; right: 24px; top: 20px; text-align: right; color: var(--white);
  }
  .holder-name { font-size: 19px; font-weight: 700; }
  .holder-title { font-size: 11px; font-weight: 400; margin-top: 3px; }

  .contact {
    position: absolute; right: 22px; top: 136px; color: var(--ink);
    font-size: 11.5px; text-align: right; line-height: 1.45;
  }
  .contact-group + .contact-group { margin-top: 14px; }
  .contact-row { display: flex; align-items: center; justify-content: flex-end; gap: 7px; }
  .contact-icon { width: 11px; height: 11px; flex: none; }
  .contact-icon.blank { visibility: hidden; }
</style>
</head>
<body>
<main class="stage">

  <section class="card card-front" aria-label="Card front">
    <div class="brand">
      <span class="brand-square"></span>
      <span class="brand-name">Veldmark Supplies</span>
    </div>
    <div class="edge-stripe"></div>
  </section>

  <section class="card card-back" aria-label="Card back">
    <svg class="card-art" viewBox="0 0 520 297" aria-hidden="true">
      <path d="M0,0 H520 V62 C430,88 330,70 240,100 C150,130 70,118 0,150 Z" fill="var(--brand-red)"/>
      <path d="M520,80 C430,108 330,88 240,118 C150,148 70,138 0,168" fill="none" stroke="var(--brand-blue)" stroke-width="6"/>
      <path d="M0,180 C60,150 120,145 190,140" fill="none" stroke="var(--brand-blue)" stroke-width="4"/>
    </svg>

    <div class="holder">
      <div class="holder-name">Dana Reyes</div>
      <div class="holder-title">Managing Director</div>
    </div>

    <div class="contact">
      <div class="contact-group">
        <div class="contact-row">412 W. Marlow Ave Suite 5
          <svg class="contact-icon" viewBox="0 0 12 12"><circle cx="6" cy="6" r="6" fill="var(--brand-red)"/><path d="M6 2.5a2.2 2.2 0 0 0-2.2 2.2C3.8 6.4 6 9.5 6 9.5s2.2-3.1 2.2-4.8A2.2 2.2 0 0 0 6 2.5z" fill="var(--white)"/></svg>
        </div>
        <div class="contact-row">Midland, Tx 79701<svg class="contact-icon blank" viewBox="0 0 12 12"></svg></div>
      </div>
      <div class="contact-group">
        <div class="contact-row">(432)555-0187
          <svg class="contact-icon" viewBox="0 0 12 12"><circle cx="6" cy="6" r="6" fill="var(--brand-red)"/><path d="M3.6 3.2l1.3-.4.8 1.6-.8.6a4 4 0 0 0 1.9 1.9l.6-.8 1.6.8-.4 1.3C6 8.6 3.4 6 3.6 3.2z" fill="var(--white)"/></svg>
        </div>
        <div class="contact-row">sales@veldmarksupplies.com
          <svg class="contact-icon" viewBox="0 0 12 12"><circle cx="6" cy="6" r="6" fill="var(--brand-red)"/><rect x="3" y="4" width="6" height="4.2" fill="var(--white)"/><path d="M3 4l3 2.3L9 4" fill="none" stroke="var(--brand-red)" stroke-width=".7"/></svg>
        </div>
        <div class="contact-row">www.veldmarksupplies.com
          <svg class="contact-icon" viewBox="0 0 12 12"><circle cx="6" cy="6" r="6" fill="var(--brand-red)"/><circle cx="6" cy="6" r="3" fill="none" stroke="var(--white)" stroke-width=".8"/><path d="M3 6h6M6 3c-1.4 1.6-1.4 4.4 0 6M6 3c1.4 1.6 1.4 4.4 0 6" fill="none" stroke="var(--white)" stroke-width=".6"/></svg>
        </div>
      </div>
    </div>

    <div class="brand">
      <span class="brand-square"></span>
      <span class="brand-name">Veldmark Supplies</span>
    </div>
  </section>

</main>
</body>
</html>
```